We need a new business card that reflects who we are. Professional, classy, modern, and service ori

We need a business card design for a window coverings design company in Kansas City called Bright Lane Interiors. We offer professional, modern, and high quality window covering products. We are looking to portray an image of a big, national franchise. We are a 5 location (with showrooms) business with 10 professional designers and 4 professional installers. These cards will be used with Thank you cards, given to realtors, and asked for referrals with.

Target Market(s)

Kansas City

Industry/Entity Type

Business

Contact Information for Business Card

We would like our card to look clean and simple on the front, featuring our logo and Marlow Fenwick's. Our designers' phone numbers and emails should be displayed as well as their title.

Font styles to use
Sans Serif

Colors

Designer to choose colors to be used in the design.

Requirements
Must have
• Front - Logos, name, phone number, email address
• Back - Showroom locations, social media? Appt date/time?
Nice to have
• I would like a clean and modern look (not contemporary. I like a white background, but I am open to ideas. Looking for a "National chain" look for a small business.
Should not have
• Too much busyness.

```html
<!DOCTYPE html>
<html lang="en">
<head>
<meta charset="utf-8">
<title>Bright Lane Interiors – Business Card</title>
<link rel="stylesheet" href="https://fonts.googleapis.com/css2?family=Roboto:wght@400;500;700&family=Roboto+Condensed:wght@400;700&display=swap">
<style>
  :root {
    --brand-red: #c54246;
    --brand-grey: #9a9b9d;
    --ink: #1a1a1a;
    --text-grey: #555759;
    --partner-grey: #5c6570;
    --partner-accent: #f08a1c;
    --card-white: #f4f4f4;
    --backdrop: #2c2c2c;
  }
  * { box-sizing: border-box; margin: 0; padding: 0; }
  html, body {
    width: 1200px; height: 960px; overflow: hidden;
    background: var(--backdrop);
    font-family: "Roboto", Arial, sans-serif;
  }
  .card {
    position: absolute; width: 600px; height: 343px;
    background: var(--card-white);
    box-shadow: 0 2px 6px rgba(0,0,0,.45);
  }
  .card--front { left: 314px; top: 113px; }
  .card--back  { left: 311px; top: 472px; }

  .brand { position: absolute; text-align: center; color: var(--ink); }
  .brand__name { font-size: 23px; font-weight: 500; letter-spacing: .2px; white-space: nowrap; display: flex; align-items: center; gap: 8px; justify-content: center; }
  .brand__mark { width: 14px; height: 14px; background: var(--brand-red); display: inline-block; }
  .brand__tagline { font-size: 12px; margin-top: 6px; color: var(--ink); }
  .card--front .brand { right: 64px; top: 120px; }
  .card--back .brand { right: 60px; top: 70px; }

  .name-band {
    position: absolute; left: 0; top: 237px; width: 293px; height: 61px;
    background: var(--brand-red);
    border-right: 8px solid var(--brand-grey);
    padding: 9px 0 0 43px;
    font-family: "Roboto Condensed", Arial, sans-serif;
  }
  .name-band__name { color: #fff; font-size: 24px; font-weight: 700; line-height: 25px; }
  .name-band__title { color: var(--ink); font-size: 15px; font-weight: 700; line-height: 18px; }

  .contact { position: absolute; left: 304px; top: 239px; list-style: none; }
  .contact li { display: flex; align-items: center; height: 19px; font-size: 14.5px; color: var(--text-grey); }
  .contact svg { width: 13px; height: 13px; margin-right: 9px; fill: var(--brand-red); }

  .appointment { position: absolute; left: 43px; top: 87px; width: 500px; color: var(--brand-red); }
  .appointment__heading { font-size: 21px; font-weight: 500; margin-bottom: 29px; }
  .field-row { display: flex; align-items: baseline; font-size: 16px; height: 41px; }
  .field-row__line { flex: 1; border-bottom: 1px dotted var(--text-grey); margin: 0 0 0 8px; height: 1px; }
  .field-row__line--date { flex: 0 0 213px; margin: 0 2px 0 6px; }
  .field-row__line--time { flex: 0 0 138px; margin: 0 4px 0 6px; }
  .field-row__suffix { font-size: 13px; }

  .locations-band {
    position: absolute; left: 0; top: 229px; width: 100%; height: 29px;
    background: var(--brand-red); color: #fff;
    font-family: "Roboto Condensed", Arial, sans-serif; font-weight: 700; font-size: 16.5px;
    line-height: 29px; padding-left: 42px; letter-spacing: .2px; white-space: nowrap;
  }
  .social { position: absolute; left: 44px; top: 280px; display: flex; gap: 3px; }
  .social span { width: 22px; height: 22px; border-radius: 50%; background: var(--brand-red); }

  .partner {
    position: absolute; right: 56px; top: 279px;
    display: flex; align-items: center; gap: 6px;
    font-family: "Roboto Condensed", Arial, sans-serif; font-weight: 700; font-size: 16px;
    color: var(--partner-grey);
  }
  .partner__dot { width: 20px; height: 20px; border-radius: 50%; background: var(--partner-accent); }
</style>
</head>
<body>

<section class="card card--front">
  <div class="brand">
    <div class="brand__name"><span class="brand__mark"></span>Bright Lane Interiors</div>
    <div class="brand__tagline">Blinds, Shades, Shutters, Draperies &amp; Decor</div>
  </div>

  <div class="name-band">
    <div class="name-band__name">ALEX MORGAN</div>
    <div class="name-band__title">DESIGNER</div>
  </div>

  <ul class="contact">
    <li>
      <svg viewBox="0 0 24 24" aria-hidden="true"><path d="M6.6 10.8a15.1 15.1 0 0 0 6.6 6.6l2.2-2.2a1 1 0 0 1 1-.25 11.4 11.4 0 0 0 3.6.57 1 1 0 0 1 1 1V20a1 1 0 0 1-1 1A17 17 0 0 1 3 4a1 1 0 0 1 1-1h3.5a1 1 0 0 1 1 1c0 1.25.2 2.45.57 3.57a1 1 0 0 1-.25 1z"/></svg>
      913.555.0148
    </li>
    <li>
      <svg viewBox="0 0 24 24" aria-hidden="true"><path d="M2 5h20v2l-10 7L2 7z M2 9l10 7 10-7v10H2z"/></svg>
      info@brightlaneinteriors.com
    </li>
    <li>
      <svg viewBox="0 0 24 24" aria-hidden="true"><path d="M12 2a10 10 0 1 0 0 20 10 10 0 0 0 0-20zm-1 17.9A8 8 0 0 1 4.1 11L9 16v1a2 2 0 0 0 2 2zm6.9-2.5A2 2 0 0 0 16 16h-1v-3a1 1 0 0 0-1-1H8v-2h2a1 1 0 0 0 1-1V7h2a2 2 0 0 0 2-2v-.4a8 8 0 0 1 2.9 12.8z"/></svg>
      brightlaneinteriors.com
    </li>
  </ul>
</section>

<section class="card card--back">
  <div class="brand">
    <div class="brand__name"><span class="brand__mark"></span>Bright Lane Interiors</div>
  </div>

  <div class="appointment">
    <h2 class="appointment__heading">Next Appointment</h2>
    <div class="field-row">Name :<span class="field-row__line"></span></div>
    <div class="field-row">Date :<span class="field-row__line field-row__line--date"></span>Time :<span class="field-row__line field-row__line--time"></span><span class="field-row__suffix">AM/PM</span></div>
  </div>

  <div class="locations-band">ASHBURY | WILLOW CREEK | FOX’S HOLLOW | NORTHVALE | ST MARLOW</div>

  <div class="social" aria-label="Social media">
    <span></span><span></span><span></span><span></span>
  </div>

  <div class="partner">Marlow Fenwick<span class="partner__dot"></span></div>
</section>

</body>
</html>
```